KRT Project Signage

Need a sign to be displayed in the front of properties currently under Construction or Renovation to advertise our company information. Need it to be Professional and Contemporary. We are a Design/Build Construction Company. Information should include Company Name, email, website, phone number. Attached: Logo and company brochure, also included and inspiration images

```html
<!DOCTYPE html>
<html lang="en">
<head>
<meta charset="utf-8">
<title>KRT Construction — Project Sign</title>
<link rel="stylesheet" href="https://fonts.googleapis.com/css2?family=Montserrat:wght@400;500;600;700;800&display=swap">
<style>
  :root {
    --backdrop: #e5e5e5;
    --charcoal: #333333;
    --white: #ffffff;
    --accent-yellow: #f2e840;
  }
  * { margin: 0; padding: 0; box-sizing: border-box; }
  html, body {
    width: 1200px; height: 1200px; overflow: hidden;
    background: var(--backdrop);
    font-family: "Montserrat", Arial, sans-serif;
  }
  .sign {
    position: absolute; left: 234px; top: 70px;
    width: 732px; height: 1060px;
    background: var(--charcoal);
    box-shadow: 6px 8px 8px rgba(0,0,0,0.35);
    overflow: hidden;
  }
  .sign-shapes { position: absolute; left: 0; top: 0; }
  .brand {
    position: absolute; left: 0; right: 0; top: 140px;
    display: flex; justify-content: center; align-items: center; gap: 18px;
  }
  .brand-name {
    font-weight: 600; font-size: 42px; letter-spacing: 2px;
    color: var(--charcoal); white-space: nowrap;
  }
  .brand-dot {
    width: 46px; height: 46px; border-radius: 50%;
    background: var(--accent-yellow);
  }
  .service {
    position: absolute; left: 121px; width: 491px; top: 427px; height: 86px;
    border-top: 2px solid var(--white); border-bottom: 2px solid var(--white);
    display: flex; align-items: center; justify-content: center;
  }
  .service-title {
    color: var(--white); font-weight: 500; font-size: 60px; letter-spacing: 3px;
    line-height: 1; white-space: nowrap; flex-shrink: 0;
  }
  .contact-icon {
    position: absolute; left: 50%; transform: translateX(-50%);
    border-radius: 50%; background: var(--white);
    display: flex; align-items: center; justify-content: center;
  }
  .icon-phone { top: 553px; width: 70px; height: 70px; }
  .icon-mail { top: 707px; width: 66px; height: 66px; }
  .icon-pin { top: 835px; width: 62px; height: 62px; }
  .contact-text {
    position: absolute; left: 0; right: 0; text-align: center; color: var(--white);
    white-space: nowrap;
  }
  .phone { top: 622px; font-size: 64px; font-weight: 800; letter-spacing: -1px; }
  .email { top: 786px; font-size: 33px; font-weight: 700; }
  .address { top: 903px; font-size: 33px; font-weight: 500; line-height: 33px; letter-spacing: 0.5px; }
  .web-band {
    position: absolute; left: 0; right: 0; bottom: 0; height: 67px;
    background: var(--white);
    display: flex; align-items: center; justify-content: center;
  }
  .web {
    color: var(--charcoal); font-weight: 600; font-size: 27px; letter-spacing: 2.5px;
    white-space: nowrap;
  }
</style>
</head>
<body>
  <main class="sign">
    <svg class="sign-shapes" width="732" height="1060" viewBox="0 0 732 1060" aria-hidden="true">
      <polygon points="8,8 724,8 724,386 366,322 8,386" fill="var(--white)"/>
      <polygon points="8,395 366,331 724,395 724,405 366,340 8,405" fill="var(--white)"/>
    </svg>

    <div class="brand">
      <span class="brand-name">KRT CONSTRUCTION</span>
      <span class="brand-dot"></span>
    </div>

    <div class="service"><h1 class="service-title">DESIGN-BUILD</h1></div>

    <div class="contact-icon icon-phone">
      <svg width="40" height="40" viewBox="0 0 24 24" aria-hidden="true">
        <path fill="var(--charcoal)" d="M6.6 10.8c1.4 2.8 3.8 5.1 6.6 6.6l2.2-2.2c.3-.3.7-.4 1-.2 1.1.4 2.3.6 3.6.6.6 0 1 .4 1 1V20c0 .6-.4 1-1 1C10.6 21 3 13.4 3 4c0-.6.4-1 1-1h3.5c.6 0 1 .4 1 1 0 1.3.2 2.5.6 3.6.1.3 0 .7-.2 1z"/>
      </svg>
    </div>
    <p class="contact-text phone">555-014-2288</p>

    <div class="contact-icon icon-mail">
      <svg width="40" height="28" viewBox="0 0 40 28" aria-hidden="true">
        <rect x="1.5" y="1.5" width="37" height="25" fill="none" stroke="var(--charcoal)" stroke-width="3"/>
        <polyline points="2,2 20,16 38,2" fill="none" stroke="var(--charcoal)" stroke-width="3"/>
        <line x1="2" y1="26" x2="15" y2="12" stroke="var(--charcoal)" stroke-width="3"/>
        <line x1="38" y1="26" x2="25" y2="12" stroke="var(--charcoal)" stroke-width="3"/>
      </svg>
    </div>
    <p class="contact-text email">info@krtconstruction.com</p>

    <div class="contact-icon icon-pin">
      <svg width="30" height="40" viewBox="0 0 30 40" aria-hidden="true">
        <path fill="var(--charcoal)" d="M15 1C7.3 1 1.5 6.8 1.5 14c0 8 13.5 25 13.5 25s13.5-17 13.5-25C28.5 6.8 22.7 1 15 1zm0 19a6 6 0 1 1 0-12 6 6 0 0 1 0 12z"/>
      </svg>
    </div>
    <p class="contact-text address">1480 Harbor Ln. Ste. 310<br>Palm Grove, FL 33000</p>

    <footer class="web-band"><span class="web">WWW.KRTCONSTRUCTION.COM</span></footer>
  </main>
</body>
</html>
```